Business card for medical clinic

I need an upmarket, modern medical/health business card for my clinic

Contact Information for Business Card

name, address, email, qr code

```html
<!DOCTYPE html>
<html lang="en">
<head>
<meta charset="utf-8">
<title>Larkstone Health Partners — Business Card</title>
<link rel="stylesheet" href="https://fonts.googleapis.com/css2?family=Cinzel:wght@500&family=Noto+Serif:wght@400&display=swap">
<style>
  :root {
    --backdrop: #d3d4d6;
    --navy: #2a2e44;
    --steel: #3f6b92;
    --sky: #2fb4e8;
    --ink: #1c1c22;
    --brand-blue: #1f5d8f;
    --accent-blue: #1ea3e0;
    --white: #ffffff;
  }
  * { box-sizing: border-box; margin: 0; padding: 0; }
  html, body {
    width: 900px;
    height: 1200px;
    overflow: hidden;
    background: var(--backdrop);
  }
  .sheet {
    position: relative;
    width: 900px;
    height: 1200px;
  }
  .card {
    position: absolute;
    left: 133px;
    width: 633px;
    height: 364px;
  }
  .card-front {
    top: 210px;
    background: linear-gradient(180deg, var(--navy) 0%, #323a56 28%, var(--steel) 58%, #3a9bcc 82%, var(--sky) 100%);
    display: flex;
    align-items: center;
    justify-content: center;
  }
  .front-brand {
    display: flex;
    align-items: center;
    gap: 16px;
    white-space: nowrap;
  }
  .brand-dot {
    width: 12px;
    height: 12px;
    border-radius: 50%;
    background: var(--white);
    flex: none;
  }
  .front-brand-name {
    font-family: "Noto Serif", serif;
    font-weight: 400;
    font-size: 29px;
    letter-spacing: 1.5px;
    color: var(--white);
  }
  .card-back {
    top: 624px;
    background: var(--white);
    text-align: center;
  }
  .holder-name {
    position: absolute;
    top: 68px;
    left: 0;
    right: 0;
    font-family: "Cinzel", serif;
    font-weight: 500;
    font-size: 23px;
    letter-spacing: 0.5px;
    color: var(--brand-blue);
  }
  .holder-role {
    position: absolute;
    top: 96px;
    left: 50%;
    transform: translateX(-50%);
    display: flex;
    align-items: center;
    gap: 8px;
    font-family: "Noto Serif", serif;
    font-size: 15px;
    color: var(--accent-blue);
    white-space: nowrap;
  }
  .holder-role::before,
  .holder-role::after {
    content: "";
    width: 50px;
    height: 1.5px;
    background: var(--accent-blue);
  }
  .contact {
    position: absolute;
    left: 0;
    right: 0;
    font-family: "Noto Serif", serif;
    color: var(--ink);
    white-space: nowrap;
  }
  .address { top: 129px; font-size: 14.5px; line-height: 22.5px; }
  .contact-icons {
    position: absolute;
    top: 178px;
    left: 50%;
    transform: translateX(-50%);
    display: flex;
    gap: 6px;
  }
  .contact-icons svg { width: 12px; height: 12px; }
  .phone { top: 204px; font-size: 14.5px; letter-spacing: 3px; }
  .email { top: 228px; font-size: 14.5px; }
  .web { top: 253px; font-size: 14.5px; }
  .back-brand {
    position: absolute;
    top: 300px;
    left: 50%;
    transform: translateX(-50%);
    display: flex;
    align-items: center;
    gap: 7px;
    white-space: nowrap;
  }
  .back-brand .brand-dot {
    width: 8px;
    height: 8px;
    background: var(--brand-blue);
  }
  .back-brand-name {
    font-family: "Noto Serif", serif;
    font-size: 12px;
    letter-spacing: 0.5px;
    color: var(--brand-blue);
  }
</style>
</head>
<body>
<main class="sheet">
  <section class="card card-front" aria-label="Card front">
    <div class="front-brand">
      <span class="brand-dot"></span>
      <span class="front-brand-name">LARKSTONE HEALTH PARTNERS</span>
    </div>
  </section>

  <section class="card card-back" aria-label="Card back">
    <h1 class="holder-name">DANIEL WHITMORE</h1>
    <p class="holder-role">Principal Consultant</p>
    <p class="contact address">PO Box 418250<br>Pine Hollow, Oregon 97412</p>
    <div class="contact-icons">
      <svg viewBox="0 0 24 24" aria-label="Phone"><path fill="#1f5d8f" d="M6.6 10.8a15 15 0 0 0 6.6 6.6l2.2-2.2c.3-.3.7-.4 1-.2 1.1.4 2.3.6 3.6.6.6 0 1 .4 1 1V20c0 .6-.4 1-1 1C10.6 21 3 13.4 3 4c0-.6.4-1 1-1h3.5c.6 0 1 .4 1 1 0 1.3.2 2.5.6 3.6.1.3 0 .7-.2 1z"/></svg>
      <svg viewBox="0 0 24 24" aria-label="Email"><rect x="2" y="5" width="20" height="14" fill="#1f5d8f"/><path d="M2 5l10 8 10-8" fill="none" stroke="#fff" stroke-width="1.6"/></svg>
      <svg viewBox="0 0 24 24" aria-label="Website"><g fill="none" stroke="#1f5d8f" stroke-width="1.8"><circle cx="12" cy="12" r="9.5"/><ellipse cx="12" cy="12" rx="4" ry="9.5"/><path d="M2.5 12h19M4 7h16M4 17h16"/></g></svg>
    </div>
    <p class="contact phone">+1-555-014-2736</p>
    <p class="contact email">info@larkstonehealthpartners.com</p>
    <p class="contact web">www.larkstonehealthpartners.com</p>
    <div class="back-brand">
      <span class="brand-dot"></span>
      <span class="back-brand-name">LARKSTONE HEALTH PARTNERS</span>
    </div>
  </section>
</main>
</body>
</html>
```